Local fast-growing company in the service sector

We are looking for a modern business card design, which should also appear on our letterheads

Target Market(s)

Private and industrial sectors

Contact Information for Business Card

Vorname Name
Kellberger Str. 18
72814 Kellbach
Tel.: 07146-839214-0
Name@agentur-kvtl.de

Colors
9d9d9d
919191
aaaaaa

Requirements
Must have
• The logo (file) in silver

```html
<!DOCTYPE html>
<html lang="de">
<head>
<meta charset="utf-8">
<title>KVTL Visitenkarte</title>
<link rel="stylesheet" href="https://fonts.googleapis.com/css2?family=Exo+2:wght@400;500;700&display=swap">
<style>
  :root {
    --page: #e2e2e2;
    --card-dark: #252525;
    --card-mid: #3a3a3a;
    --silver: #aaaaaa;
    --silver-light: #c4c4c4;
    --silver-dark: #919191;
    --text-light: #e6e6e6;
    --white: #ffffff;
  }
  * { margin: 0; padding: 0; box-sizing: border-box; }
  html, body {
    width: 1200px; height: 576px; overflow: hidden;
    background: var(--page);
    font-family: "Exo 2", sans-serif;
  }
  .canvas { position: relative; width: 1200px; height: 576px; }
  .card {
    position: absolute; top: 138px;
    width: 484px; height: 294px; border-radius: 13px;
    background: radial-gradient(ellipse at 50% 35%, var(--card-mid) 0%, var(--card-dark) 75%);
    box-shadow: 0 2px 5px rgba(0,0,0,.35);
    overflow: hidden;
  }
  .card--front { left: 82px; }
  .card--back { left: 602px; width: 480px; }

  .brand__square { position: absolute; background: var(--silver); }
  .brand__name {
    position: absolute; color: var(--silver);
    font-weight: 700; line-height: 1; white-space: nowrap;
  }

  .front-square { left: 92px; top: 98px; width: 96px; height: 96px; }
  .front-name { left: 198px; top: 118px; font-size: 68px; letter-spacing: 3px; }
  .front-web {
    position: absolute; left: 200px; top: 180px;
    color: var(--silver); font-size: 18px; font-weight: 500;
    letter-spacing: 1.5px; line-height: 1; white-space: nowrap;
  }

  .back-square { left: 80px; top: 72px; width: 100px; height: 100px; }
  .back-name { left: 78px; top: 186px; font-size: 30px; letter-spacing: 2px; }

  .contact { position: absolute; left: 240px; top: 94px; color: var(--text-light); }
  .contact__name {
    font-weight: 700; font-size: 17px; letter-spacing: 2.5px; line-height: 20px;
    color: var(--white); margin-bottom: 16px; white-space: nowrap;
  }
  .contact__line {
    font-size: 14px; font-weight: 500; line-height: 17.5px; letter-spacing: .3px;
    display: flex; align-items: center; white-space: nowrap;
  }
  .contact__icon { width: 11px; height: 11px; margin-right: 13px; fill: var(--text-light); flex: none; }
</style>
</head>
<body>
<main class="canvas">
  <section class="card card--front" aria-label="Vorderseite">
    <span class="brand__square front-square"></span>
    <span class="brand__name front-name">KVTL</span>
    <p class="front-web">agentur-kvtl.de</p>
  </section>

  <section class="card card--back" aria-label="Rückseite">
    <span class="brand__square back-square"></span>
    <span class="brand__name back-name">KVTL</span>
    <div class="contact">
      <p class="contact__name">VORNAME NAME</p>
      <p class="contact__line">Kellberger Str. 18</p>
      <p class="contact__line">72814 Kellbach</p>
      <p class="contact__line">
        <svg class="contact__icon" viewBox="0 0 12 12" aria-hidden="true"><path d="M1 4c0-2 2-3 5-3s5 1 5 3l-2 1-1-2H4L3 5 1 4zm2 2h6l1 5H2l1-5zm3 1a1.5 1.5 0 100 3 1.5 1.5 0 000-3z"/></svg>
        07146-839214-0
      </p>
      <p class="contact__line">
        <svg class="contact__icon" viewBox="0 0 12 12" aria-hidden="true"><path d="M0 2h12v8H0zM1 3l5 4 5-4v-.2H1z" fill-rule="evenodd"/></svg>
        Name@agentur-kvtl.de
      </p>
    </div>
  </section>
</main>
</body>
</html>
```